Highlight Document Over Image for Slide

We are seeking a graphic designer to overlay a news article on an image that pertains to the article, aiming for a stylish yet professional appearance. Given the limited resources, we encourage you to use your imagination and go beyond what basic tools like PowerPoint can offer.

```html
<!DOCTYPE html>
<html lang="en">
<head>
<meta charset="utf-8">
<title>Contraband Items Slide</title>
<link rel="stylesheet" href="https://fonts.googleapis.com/css2?family=Tinos:wght@400;700&family=Poppins:wght@400&display=swap">
<style>
  :root {
    --page-bg: #eeeeee;
    --paper: #ffffff;
    --ink: #111111;
    --frame: #000000;
    --frame-ring: #ffffff;
    --sepia-top: #8c7b5a;
    --sepia-mid: #6f6249;
    --sepia-low: #5c5040;
    --hill-gold: #a88a52;
    --hill-green: #6e6a48;
    --shore: #6a6658;
    --water: #55534b;
  }
  * { box-sizing: border-box; margin: 0; padding: 0; }
  html, body {
    width: 1200px; height: 1200px; overflow: hidden;
    background: var(--page-bg);
  }
  .slide {
    position: absolute; left: 25px; top: 242px;
    width: 1155px; height: 649px; overflow: hidden;
    box-shadow: 0 2px 6px rgba(0,0,0,0.35);
  }
  .backdrop-view {
    position: absolute; inset: 0;
    background:
      radial-gradient(ellipse 30% 40% at 8% 80%, #7a6c55 0%, rgba(122,108,85,0) 70%),
      linear-gradient(180deg, var(--sepia-top) 0%, var(--sepia-mid) 45%, var(--sepia-low) 100%);
  }
  .screen-frame {
    position: absolute; left: 112px; top: 109px;
    width: 938px; height: 560px;
    background: var(--frame);
    border: 3px solid var(--frame-ring);
    border-radius: 38px 38px 0 0;
  }
  .screen-view {
    position: absolute; left: 143px; top: 149px;
    width: 876px; height: 500px;
    background:
      radial-gradient(ellipse 22% 30% at 60% 72%, #8a7358 0%, rgba(138,115,88,0) 70%),
      linear-gradient(180deg, var(--hill-gold) 0%, var(--hill-green) 22%, var(--shore) 48%, var(--water) 70%, var(--water) 100%);
  }
  .headline-box, .body-box, .body-tail {
    position: absolute; background: var(--paper); color: var(--ink);
    font-family: "Tinos", "Times New Roman", serif;
  }
  .headline-box {
    left: 194px; top: 512px; width: 648px; height: 28px;
    border-radius: 7px 7px 0 0;
    padding: 0 8px;
    font-weight: 700; font-size: 22px; line-height: 30px;
    white-space: nowrap;
  }
  .body-box {
    left: 194px; top: 540px; width: 823px; height: 177px;
    border-radius: 0 7px 7px 0;
    padding: 0 9px;
    font-size: 22px; line-height: 29.5px;
  }
  .body-line { display: block; text-align: justify; text-align-last: justify; white-space: nowrap; }
  .body-tail {
    left: 194px; top: 717px; width: 304px; height: 28px;
    border-radius: 0 0 7px 7px;
    padding: 0 9px;
    font-size: 22px; line-height: 22px;
    white-space: nowrap;
  }
  .page-number {
    position: absolute; left: 561px; top: 805px;
    width: 88px; height: 42px; border-radius: 21px;
    background: var(--frame); border: 3px solid var(--frame-ring);
    color: #fff; font-family: "Poppins", Arial, sans-serif;
    font-size: 14px; letter-spacing: 4px;
    display: flex; align-items: center; justify-content: center;
    padding-left: 4px;
  }
</style>
</head>
<body>
  <section class="slide">
    <div class="backdrop-view" role="img" aria-label="Sepia-toned aerial map of a waterfront hillside with winding roads"></div>
    <div class="screen-frame"></div>
    <div class="screen-view" role="img" aria-label="Colour satellite view of a bayside correctional facility, hillside roads and water"></div>
  </section>

  <h1 class="headline-box">INTRODUCTION OR POSSESSION OF CONTRABAND ITEMS</h1>
  <p class="body-box">
    <span class="body-line">Employees shall not introduce or possess unauthorized items such as escape</span>
    <span class="body-line">paraphernalia, weapons, facsimiles of weapons, ammunition, wireless communication</span>
    <span class="body-line">devices, cell phones, tobacco or facsimiles of tobaccos products (e.g. electronic vapor</span>
    <span class="body-line">cigarettes) lighters or any other item not specifically authorized by PD 04.04.100</span>
    <span class="body-line">“Custody, Security and Safety Systems (Exempt)”, OP 04.04.100 “Gate Security” or</span>
    <span class="body-line">facility operating procedure in any facility where offenders are housed. Employees are</span>
  </p>
  <p class="body-tail">responsible for any item in their</p>

  <div class="page-number">36</div>
</body>
</html>
```